Moxy Fen needs some awesome stationary

Do you have what it takes to get my brand? You either do or you don't, have a crack at a design and you my just win my business.

I don't want to waste your or my time, so put your creative genius on either a business card or envelope.

I however need a package of stationary that follows the same brand. I will message you to complete the remaining should I like your first submission.

Here is what I need, have a go!

Basically I need the following for my small business based in melbourne.
- Letterhead (printer ready and MS Word)
- Business Card
- Compliments Slip
- Envelope
- Proposal Cover Page (MS Word only)
- Presentation Folder
- Marbled Fox Cards
- Student Name Tent
- Index Cards
- Vell-Ka

I am establishing the brand and it must be modern, professional but also relaxed; that is not formal and not corporate. It represents a company are leaders, but small enough to care and operate like a bunch of friends. We are bringing people and conversations back to business, and turfing out all the bureaucracy and crazy and wasteful procedures. Its about "lets talk and figure it out together and find even better ways".

Target Market(s)

Mainly companies that build software products, but Agile practices are used in many other industries (even graphic design projects)

Industry/Entity Type

Information Technology

Font styles to use
Sans Serif

Colors
3176b5
aaaaaa

Requirements
Must have
• I like curves and circles and not boxes or rectangles.
• I want a colour rich design with my brand colours, but it must be balanced.
• I want more modern than traditional, but simple modern
Should not have
• Not corporate
• Please don't waste my time if your not going to think about it.
• Don't mess with my primary logo
• Don't change my colours
• Don't overlay logo on image

```html
<!DOCTYPE html>
<html lang="en">
<head>
<meta charset="utf-8">
<title>Moxy Fen – Compliments Slip and Envelope</title>
<link rel="stylesheet" href="https://fonts.googleapis.com/css2?family=Open+Sans:wght@400;600;700&display=swap">
<style>
  :root {
    --brand-blue: #1f5aa6;
    --brand-sky: #2f8fd8;
    --brand-grey: #9aa3af;
    --text-grey: #8a8f96;
    --paper: #ffffff;
    --pattern-light: #ececee;
    --flap-inner: #fbfbfb;
    --page-bg: #e9edf2;
    --watermark: #f1f2f8;
  }
  * { margin: 0; padding: 0; box-sizing: border-box; }
  html, body { width: 1200px; height: 1200px; overflow: hidden; }
  body {
    background: var(--page-bg);
    font-family: "Open Sans", sans-serif;
    position: relative;
  }

  /* ---------- Compliments slip ---------- */
  .slip {
    position: absolute;
    left: 100px; top: 90px;
    width: 1000px; height: 455px;
    background: var(--paper);
    overflow: hidden;
    box-shadow: 0 10px 30px rgba(20, 50, 90, 0.18);
  }
  .slip__tab-left {
    position: absolute; left: 0; top: 40px;
    width: 10px; height: 70px;
    background: var(--brand-blue);
  }
  .slip__tab-right {
    position: absolute; right: 0; top: 270px;
    width: 10px; height: 70px;
    background: var(--brand-grey);
  }
  .slip__band {
    position: absolute; left: 0; bottom: 0;
    width: 100%; height: 16px;
    background: var(--brand-sky);
    border-top: 4px solid var(--brand-blue);
  }
  .slip__watermark {
    position: absolute; right: 40px; top: 110px;
    width: 300px; height: 300px;
  }
  .brand {
    display: flex; align-items: center; gap: 12px;
  }
  .brand__dot {
    width: 44px; height: 44px; border-radius: 50%;
    background: var(--brand-blue);
  }
  .brand__name {
    font-weight: 700;
    font-size: 38px;
    color: var(--brand-blue);
    letter-spacing: -0.5px;
  }
  .slip .brand {
    position: absolute; left: 50px; top: 50px;
  }
  .contact {
    position: absolute; left: 50px; bottom: 40px;
    display: flex; gap: 48px; align-items: flex-end;
  }
  .contact__item {
    display: flex; flex-direction: column; align-items: flex-end; gap: 10px;
    font-size: 13px; color: var(--text-grey);
  }
  .contact__icon { width: 16px; height: 16px; fill: var(--brand-blue); }

  /* ---------- Envelope (back) ---------- */
  .envelope {
    position: absolute;
    left: 100px; top: 640px;
    width: 1000px; height: 470px;
    box-shadow: 0 10px 30px rgba(20, 50, 90, 0.18);
  }
  .envelope__flap {
    position: absolute; left: 0; top: 0;
    width: 100%; height: 110px;
    background: var(--brand-blue);
  }
  .envelope__body {
    position: absolute; left: 0; top: 110px;
    width: 100%; height: 360px;
    background: var(--pattern-light);
  }
  .envelope__inner {
    position: absolute; left: 0; top: 110px;
    width: 1000px; height: 150px;
  }
  .envelope .brand {
    position: absolute; left: 50%; top: 340px;
    transform: translateX(-50%);
  }
  .envelope .brand__name { font-size: 32px; }
  .envelope .brand__dot { width: 38px; height: 38px; }
</style>
</head>
<body>

  <section class="slip" aria-label="Compliments slip">
    <div class="slip__tab-left"></div>
    <div class="slip__tab-right"></div>

    <svg class="slip__watermark" viewBox="0 0 300 300" role="img" aria-label="Large faint brand circle decoration">
      <circle cx="150" cy="150" r="150" fill="var(--watermark)"/>
    </svg>

    <div class="brand">
      <span class="brand__dot"></span>
      <span class="brand__name">Moxy Fen</span>
    </div>

    <div class="contact">
      <div class="contact__item">
        <svg class="contact__icon" viewBox="0 0 16 16" aria-hidden="true"><path d="M8 0a5 5 0 0 0-5 5c0 4 5 11 5 11s5-7 5-11a5 5 0 0 0-5-5zm0 7a2 2 0 1 1 0-4 2 2 0 0 1 0 4z"/></svg>
        <span>PO Box 4417, Brindle Park, VIC 3190, Australia</span>
      </div>
      <div class="contact__item">
        <svg class="contact__icon" viewBox="0 0 16 16" aria-hidden="true"><path d="M3.5 1l2.5 3-1.5 2a9 9 0 0 0 5 5l2-1.5 3 2.5-1.5 3C7 15 1 9 .5 2.5z"/></svg>
        <span>1300 555 019</span>
      </div>
      <div class="contact__item">
        <svg class="contact__icon" viewBox="0 0 16 16" aria-hidden="true"><path d="M0 3h16v1l-8 5-8-5zm0 3l8 5 8-5v7H0z"/></svg>
        <span>hello@moxyfen.example</span>
      </div>
      <div class="contact__item">
        <svg class="contact__icon" viewBox="0 0 16 16" aria-hidden="true"><circle cx="8" cy="8" r="7.5"/><path d="M.5 8h15M8 .5c-3 3-3 12 0 15M8 .5c3 3 3 12 0 15" stroke="#fff" stroke-width="1" fill="none"/></svg>
        <span>www.moxyfen.example</span>
      </div>
    </div>

    <div class="slip__band"></div>
  </section>

  <section class="envelope" aria-label="Envelope back">
    <div class="envelope__flap" role="img" aria-label="Open flap with blue repeating brand pattern"></div>
    <div class="envelope__body" role="img" aria-label="Envelope back with light grey repeating brand pattern"></div>
    <svg class="envelope__inner" viewBox="0 0 1000 150" aria-hidden="true">
      <polygon points="25,0 975,0 880,150 120,150" fill="var(--flap-inner)"/>
    </svg>
    <div class="brand">
      <span class="brand__dot"></span>
      <span class="brand__name">Moxy Fen</span>
    </div>
  </section>

</body>
</html>
```